Award-winnning Estate Agent needs a premium version of their 'For Sale' board design

We need a premium option for our 'For Sale' board design. We have a standard board that is attached to this brief, but were are looking to have a premium design version that we will use when selling exclusive properties. Our company name is Harbourline Vale Estates and the name for this is exclusive selection is: 'The Harbourline Collection'. The design needs to work with our current brand, but have a distinctive PREMIUM feel to it. I have uploaded the barnd guidelines and also some of the exisisting logo variations. We do NOT need a new logo but feel free to play around with colours, fonts, sizes etc. for the sign.

Target Market(s)

Property buyers & house hunters

Industry/Entity Type

Real Estate - Residential Property

Font styles to use
Sans Serif

Requirements
Must have
• A premium fee, must be square design, must be easy to read when driving past the sign
Nice to have
• I'm open ot ideas

```html
<!DOCTYPE html>
<html lang="en">
<head>
<meta charset="utf-8">
<title>Harbourline Vale Estates – For Sale Board</title>
<link href="https://fonts.googleapis.com/css2?family=Arimo:wght@400;700&display=swap" rel="stylesheet">
<style>
  :root {
    --navy: #112443;
    --navy-soft: #1c2f56;
    --gold-text: #bf9262;
    --gold-mark: #cf8f52;
    --gold-band: #a57b43;
    --white: #ffffff;
  }
  html, body {
    margin: 0;
    padding: 0;
    width: 1200px;
    height: 1200px;
    overflow: hidden;
    background: var(--white);
  }
  .board {
    position: relative;
    width: 1200px;
    height: 1200px;
    background: var(--white);
    font-family: "Arimo", Helvetica, Arial, sans-serif;
  }
  .brand-panel {
    position: absolute;
    left: 34px;
    top: 34px;
    width: 1132px;
    height: 677px;
    background: var(--navy);
    overflow: hidden;
  }
  .flourish {
    position: absolute;
    top: 0;
    width: 90px;
    height: 390px;
    background: linear-gradient(180deg, rgba(28,47,86,0) 0%, var(--navy-soft) 50%, rgba(28,47,86,0) 100%);
    opacity: 0.7;
  }
  .flourish--left { left: 0; }
  .flourish--right { right: 0; }
  .brand-square {
    position: absolute;
    left: 50%;
    top: 96px;
    width: 150px;
    height: 150px;
    margin-left: -75px;
    background: var(--gold-mark);
  }
  .wordmark {
    position: absolute;
    left: 0;
    right: 0;
    top: 338px;
    margin: 0;
    text-align: center;
    font-weight: 400;
    font-size: 74px;
    letter-spacing: -1px;
    line-height: 1;
    color: var(--gold-text);
  }
  .rule {
    position: absolute;
    left: 47px;
    width: 1043px;
    height: 2px;
    background: var(--gold-text);
  }
  .rule--top { top: 484px; }
  .rule--bottom { top: 628px; }
  .collection-title {
    position: absolute;
    left: 0;
    right: 0;
    top: 524px;
    margin: 0;
    text-align: center;
    font-weight: 700;
    font-size: 63px;
    line-height: 1;
    letter-spacing: 0.5px;
    color: var(--gold-text);
    text-transform: uppercase;
  }
  .status-band {
    position: absolute;
    left: 34px;
    top: 734px;
    width: 1132px;
    height: 205px;
    background: var(--gold-band);
    display: flex;
    align-items: center;
    justify-content: center;
  }
  .status-text {
    margin: 0;
    font-weight: 700;
    font-size: 186px;
    line-height: 1;
    letter-spacing: 1px;
    color: var(--white);
  }
  .phone {
    position: absolute;
    left: 0;
    right: 0;
    top: 966px;
    margin: 0;
    text-align: center;
    font-weight: 700;
    font-size: 104px;
    line-height: 1;
    color: var(--navy);
  }
  .web {
    position: absolute;
    left: 0;
    right: 0;
    top: 1093px;
    margin: 0;
    text-align: center;
    font-weight: 400;
    font-size: 50px;
    line-height: 1;
    letter-spacing: -0.5px;
    color: var(--navy);
  }
</style>
</head>
<body>
  <main class="board">
    <section class="brand-panel">
      <div class="flourish flourish--left" role="img" aria-label="Faint navy scroll flourish decoration"></div>
      <div class="flourish flourish--right" role="img" aria-label="Faint navy scroll flourish decoration"></div>
      <div class="brand-square" aria-hidden="true"></div>
      <h1 class="wordmark">Harbourline Vale Estates</h1>
      <div class="rule rule--top" aria-hidden="true"></div>
      <h2 class="collection-title">The Harbourline Collection</h2>
      <div class="rule rule--bottom" aria-hidden="true"></div>
    </section>
    <section class="status-band">
      <p class="status-text">FOR SALE</p>
    </section>
    <p class="phone">01632 960482</p>
    <p class="web">www.harbourlinevaleestates.co.uk</p>
  </main>
</body>
</html>
```